Lunelle Rosa Hair Fancy Business Card’s

I want my business cards to be elite, original and very classy. I want the business cards to match the colors of my logo and to match the design posted. I would love the design of the picture I posted

I want the card all white .
The dripping on the top of the card I want it to match the pink color in my logo that’s also posted .
I need my logo on the business card !
I need my Instagram- @lunelle.rosa.hair__
And my phone number - 555 207 3962

Target Market(s)

My target market is young woman age 23 to older woman to the age of 65
I want both older and younger women to love my design . I don’t want any cheap looking business cards

Industry/Entity Type

Hair And Beauty

Contact Information for Business Card

Add my logo
Add my Instagram- @lunelle.rosa.hair__
My number - 555 207 3962
My website- www.lunellerosahair.example

Font styles to use
Serif
Script

Colors
ffffff
e667a6
e34298

Requirements
Must have
• The business cards must have my logo, my number , my website, and my Instagram!
Nice to have
• Nice to have glitter words that match my logo
• The business cards must look classy and mature
• I want them to be very unique!!
Should not have
• Should not have any colors that doesn’t match my logo ! This is very important! Please

```html
<!DOCTYPE html>
<html lang="en">
<head>
<meta charset="utf-8">
<title>Lunelle Rosa Hair – Business Cards</title>
<link rel="stylesheet" href="https://fonts.googleapis.com/css2?family=Montserrat:wght@400;500&display=swap">
<style>
  :root {
    --pink: #e34298;
    --pink-soft: #e667a6;
    --white: #ffffff;
    --grey: #6d6d6d;
    --backdrop: #2a2a2c;
    --card-shadow: rgba(0, 0, 0, 0.45);
  }
  * { box-sizing: border-box; margin: 0; padding: 0; }
  html, body {
    width: 1200px;
    height: 852px;
    overflow: hidden;
  }
  body {
    background: var(--backdrop);
    font-family: "Montserrat", Arial, sans-serif;
    display: flex;
    align-items: center;
    justify-content: center;
    gap: 40px;
  }
  .card {
    position: relative;
    width: 540px;
    height: 309px;
    background: var(--white);
    border-radius: 18px;
    overflow: hidden;
    box-shadow: 0 18px 40px var(--card-shadow);
  }
  .brand-name {
    position: absolute;
    left: 0;
    right: 0;
    text-align: center;
    color: var(--pink);
    font-weight: 500;
    font-size: 34px;
    letter-spacing: 2px;
  }
  .card--back .brand-name { top: 104px; }
  .card--front .brand-name { top: 92px; }

  .card--back .website {
    position: absolute;
    left: 0;
    right: 0;
    top: 220px;
    text-align: center;
    font-size: 15px;
    letter-spacing: 2.5px;
    color: var(--grey);
    font-weight: 400;
  }
  .card--back .website .domain { color: var(--pink-soft); }

  .contact-band {
    position: absolute;
    left: 0;
    right: 0;
    bottom: 22px;
    height: 30px;
    background: var(--pink);
    display: flex;
    align-items: center;
    justify-content: space-around;
    padding: 0 16px;
    color: var(--white);
    font-size: 13px;
    font-weight: 500;
    letter-spacing: 0.3px;
  }
  .contact-item {
    display: flex;
    align-items: center;
    gap: 6px;
    white-space: nowrap;
  }
  .contact-item svg { width: 12px; height: 12px; flex: none; }
</style>
</head>
<body>

  <section class="card card--back" aria-label="Business card back">
    <div class="brand-name">Lunelle Rosa Hair</div>
    <p class="website">www.<span class="domain">lunellerosahair</span>.example</p>
  </section>

  <section class="card card--front" aria-label="Business card front">
    <div class="brand-name">Lunelle Rosa Hair</div>
    <div class="contact-band">
      <span class="contact-item">
        <svg viewBox="0 0 24 24" aria-hidden="true"><path fill="#ffffff" d="M6.6 10.8a15.1 15.1 0 0 0 6.6 6.6l2.2-2.2a1 1 0 0 1 1-.25 11.4 11.4 0 0 0 3.6.57 1 1 0 0 1 1 1V20a1 1 0 0 1-1 1A17 17 0 0 1 3 4a1 1 0 0 1 1-1h3.5a1 1 0 0 1 1 1c0 1.25.2 2.45.57 3.6a1 1 0 0 1-.25 1z"/></svg>
        555 207 3962
      </span>
      <span class="contact-item">
        <svg viewBox="0 0 24 24" aria-hidden="true"><circle cx="12" cy="12" r="9" fill="none" stroke="#ffffff" stroke-width="2.5"/></svg>
        @lunelle.rosa.hair__
      </span>
      <span class="contact-item">
        <svg viewBox="0 0 24 24" aria-hidden="true"><g fill="none" stroke="#ffffff" stroke-width="2"><circle cx="12" cy="12" r="9"/><ellipse cx="12" cy="12" rx="4" ry="9"/><path d="M3 12h18"/></g></svg>
        www.lunellerosahair.example
      </span>
    </div>
  </section>

</body>
</html>
```